Crestline Build Advisors Trade Show

We need the design for tree retractable banners for a trade show. Each banner is 33.5"x 78.7" I'm attaching a sample of a possible lay out. Also you can check on our web site (currently under construction) about the language we use on it. We want something similar in the three (3) banners. The following is the link: http://cba2.pelvaronsites.net/#services. In addition, I have attached the logos of some of our clients that we would like to incorporate in the banners.
Please do not hesitate to contact me with any questions

Target Market(s)

Architects, Developers, Real Estate Companies, Construction Companies

Requirements
Must have
• Clients and Services... See web site for referencing
• http://cba2.pelvaronsites.net

```html
<!DOCTYPE html>
<html lang="en">
<head>
<meta charset="utf-8">
<title>Crestline Build Advisors – Trade Show Banners</title>
<link rel="stylesheet" href="https://fonts.googleapis.com/css2?family=Lato:wght@700;900&family=Roboto+Condensed:wght@700&display=swap">
<style>
  :root {
    --backdrop: #e9eaeb;
    --paper: #ffffff;
    --panel-grey: #f1f1f1;
    --orange: #e3731b;
    --orange-deep: #d4600f;
    --orange-light: #ef9a3a;
    --green: #7fc93a;
    --green-dark: #4ea52c;
    --blue: #2e9be0;
    --navy: #1d3f9a;
    --ink: #2b2b2b;
    --rule: #3a3a3a;
    --badge-dark: #222222;
    --badge-grey: #b9bcbe;
    --badge-blue: #3d8fd9;
  }
  * { margin: 0; padding: 0; box-sizing: border-box; }
  html, body { width: 1200px; height: 928px; overflow: hidden; }
  body {
    background: var(--backdrop);
    font-family: "Lato", sans-serif;
    position: relative;
  }
  .banner {
    position: absolute;
    top: 64px;
    width: 340px;
    height: 800px;
    overflow: hidden;
  }
  .banner svg.banner-art { position: absolute; inset: 0; }
  .banner--brand { left: 45px; }
  .banner--services { left: 430px; }
  .banner--statement { left: 815px; }

  /* Brand banner */
  .brand-name {
    position: absolute; top: 182px; left: 0; width: 340px;
    text-align: center; font-weight: 900; font-size: 21px;
    letter-spacing: 0.5px; color: var(--green-dark);
  }
  .headline {
    position: absolute; top: 320px; left: 0; width: 340px;
    text-align: center; color: var(--paper);
    font-weight: 900; font-size: 35px; line-height: 1.2;
  }
  .tagline {
    position: absolute; top: 438px; left: 0; width: 340px;
    text-align: center; color: var(--paper);
    font-family: "Roboto Condensed", sans-serif; font-weight: 700;
    font-size: 19px; line-height: 1.4;
  }

  /* Services banner */
  .service-label {
    position: absolute; text-align: center; color: var(--ink);
    font-family: "Roboto Condensed", sans-serif; font-weight: 700;
    font-size: 19px; line-height: 1.15;
  }
  .service-label--energy { left: 20px; top: 238px; width: 140px; }
  .service-label--commissioning { left: 160px; top: 256px; width: 170px; }
  .service-label--incentive { left: 10px; top: 458px; width: 160px; }
  .service-label--project { left: 175px; top: 458px; width: 160px; }
  .service-label--gap { left: 90px; top: 680px; width: 180px; }

  /* Statement banner */
  .statement {
    position: absolute; top: 560px; left: 30px; width: 280px;
    text-align: center; color: var(--paper);
    font-family: "Roboto Condensed", sans-serif; font-weight: 700;
    font-size: 19px; line-height: 1.38;
  }
</style>
</head>
<body>

<!-- Banner 1: brand and partners -->
<section class="banner banner--brand">
  <svg class="banner-art" viewBox="0 0 340 800" width="340" height="800">
    <rect width="340" height="800" fill="var(--paper)"/>
    <circle class="brand-mark" cx="170" cy="105" r="52" fill="var(--orange)"/>
    <path class="band-edge" d="M0,250 Q170,300 340,222 L340,236 Q170,316 0,264 Z" fill="var(--blue)"/>
    <path class="band" d="M0,262 Q170,314 340,234 L340,590 Q170,540 0,606 Z" fill="var(--orange)"/>
    <path class="band-foot" d="M0,606 Q170,540 340,590 L340,602 Q170,552 0,620 Z" fill="var(--green)"/>
    <g class="partner-badges">
      <circle cx="95" cy="672" r="38" fill="var(--badge-dark)"/>
      <circle cx="235" cy="672" r="36" fill="none" stroke="var(--badge-grey)" stroke-width="6"/>
      <rect x="45" y="720" width="100" height="34" rx="4" fill="var(--green)"/>
      <rect x="185" y="716" width="110" height="40" rx="4" fill="var(--badge-grey)"/>
      <rect x="110" y="764" width="120" height="30" rx="2" fill="var(--badge-blue)"/>
    </g>
  </svg>
  <div class="brand-name">CRESTLINE BUILD ADVISORS</div>
  <h1 class="headline">SUSTAINABILITY<br>CONSULTANTS</h1>
  <p class="tagline">Providing Solutions For<br>The Build Environment</p>
</section>

<!-- Banner 2: services -->
<section class="banner banner--services">
  <svg class="banner-art" viewBox="0 0 340 800" width="340" height="800">
    <defs>
      <linearGradient id="gapTones" x1="0" y1="0" x2="1" y2="0">
        <stop offset="0" stop-color="#f2b6a0"/>
        <stop offset="0.5" stop-color="#cfe6b4"/>
        <stop offset="1" stop-color="#b4c4e6"/>
      </linearGradient>
      <linearGradient id="energyTones" x1="0" y1="0" x2="1" y2="1">
        <stop offset="0" stop-color="#cfe9b3"/>
        <stop offset="1" stop-color="#b9c6e8"/>
      </linearGradient>
    </defs>
    <rect width="340" height="800" fill="var(--panel-grey)"/>
    <path class="top-cap" d="M0,0 H340 V14 Q170,88 0,14 Z" fill="var(--orange)"/>
    <path class="top-cap-edge" d="M0,14 Q170,88 340,14" fill="none" stroke="var(--green)" stroke-width="5"/>

    <g class="grid-rules" fill="none" stroke="var(--rule)" stroke-width="3">
      <polyline points="28,90 155,90 155,300 312,300"/>
      <polyline points="28,512 177,512"/>
      <polyline points="177,302 177,528 297,528 297,715"/>
    </g>

    <circle cx="90" cy="160" r="50" fill="url(#energyTones)" role="img" aria-label="Lightning bolt inside circular arrows, energy modeling icon"/>

    <circle cx="245" cy="190" r="52" fill="var(--navy)" role="img" aria-label="Technician in hard hat with gear, commissioning icon"/>

    <rect x="30" y="306" width="112" height="140" rx="8" fill="var(--green)" opacity="0.85" role="img" aria-label="Figure holding a dollar banknote, incentive icon"/>

    <rect x="195" y="318" width="112" height="128" rx="6" fill="#f3dcd2" role="img" aria-label="Triangle of arrows for scope, time and cost"/>

    <rect x="70" y="566" width="175" height="100" rx="6" fill="url(#gapTones)" role="img" aria-label="Bar chart with pulse line and magnifying glass, gap analysis illustration"/>

    <path class="bottom-cap" d="M0,800 V770 Q170,716 340,770 V800 Z" fill="var(--orange)"/>
    <path class="bottom-cap-edge" d="M0,768 Q170,712 340,768" fill="none" stroke="var(--green)" stroke-width="6"/>
  </svg>
  <div class="service-label service-label--energy">ENERGY<br>MODELING</div>
  <div class="service-label service-label--commissioning">COMMISSIONING</div>
  <div class="service-label service-label--incentive">INCENTIVE<br>Pursuit</div>
  <div class="service-label service-label--project">Project<br>Management</div>
  <div class="service-label service-label--gap">GAP Analyasis</div>
</section>

<!-- Banner 3: statement -->
<section class="banner banner--statement">
  <svg class="banner-art" viewBox="0 0 340 800" width="340" height="800">
    <defs>
      <linearGradient id="statementOrange" x1="0" y1="0" x2="0" y2="1">
        <stop offset="0" stop-color="var(--orange-deep)"/>
        <stop offset="0.5" stop-color="var(--orange)"/>
        <stop offset="1" stop-color="var(--orange-deep)"/>
      </linearGradient>
      <linearGradient id="emblemTones" x1="0" y1="0" x2="1" y2="1">
        <stop offset="0" stop-color="#f6b35a"/>
        <stop offset="0.5" stop-color="#8fcf58"/>
        <stop offset="1" stop-color="#5aaee8"/>
      </linearGradient>
    </defs>
    <rect width="340" height="800" fill="url(#statementOrange)"/>
    <path class="swoosh" d="M175,0 H340 V520 Q200,520 150,400 Q100,260 140,110 Q155,40 175,0 Z" fill="var(--paper)"/>
    <path d="M178,20 H330 V490 Q210,490 172,390 Q130,270 160,120 Q168,60 178,20 Z" fill="url(#emblemTones)" opacity="0.55" role="img" aria-label="Large brand emblem decoration in leaf green, sun orange and water blue"/>
  </svg>
  <p class="statement">A turnkey, hands-on sustainability solutions provider. We bridge the gap between capital and operating budgets with our integrated approach.</p>
</section>

</body>
</html>
```